Start-Up für Training, Coaching & Consulting sucht modernes Webdesign!
Zielgruppe
Wer ist TAVI Training, Coaching & Consulting?
Wir führen Führungskräftetrainings durch, machen Privatkunden für Bewerbungen fit und unterstützen Unternehmen mit Verkaufstrainings. Wir entwickeln Persönlichkeiten im Coaching. Wir beraten Unternehmen und helfen ihnen dabei, ihre Geschäftsabläufe und Prozesse zu optimieren. Dabei steht unsere hohe Qualität im Mittelpunkt - gemeinsam mit unseren kreativen Trainingsmethoden. Unser Background (Diplom-Kaufleute und geprüfte Trainer) bietet dafür die passende Ausgangslage.
Was bedeutet TAVI?
Tavi ist Maori und bdeutet Kreis/Spirale. Er symbolisiert einen wachsenden Silberfarn und steht für persönliche Entwicklung und Entfaltung. Der Tavi ist einerseits unser Namensgeber und unser Logo, andererseits steht der Tavi aber auch für unsere Werte: Denn wir wollen unseren Kunden dabei helfen zu wachsen und sich weiterzuentwickeln - und dies auf eine hochqualitative und seriöse Art und Weise ohne den Eindruck von Esoterik oder Erlebnispädagogik zu vermitteln.
Aufgabenstellung
Modernes Design, das unsere Philosophie widerspiegelt: Wir möchten unseren Kunden auf seriöse und hochqualitative Weise weiterentwickeln. Wir stehen für nachhaltigen Lernerfolg, kreative Trainingsmethoden, Abwechslung, Spaß am Lernen, Qualität, Kompetenz, Fachwissen und Dynamik.
Layout:
1) Header: QMSR geprüfter Trainer, Menüpunkte (siehe Architektur)
2) Banner
3) 3 Teaser (Training, Coaching, Consulting) + Header + 2-3 Zeilen Text (+Icons)
>>> Sichtbarer Bereich auf Homepage: Menü, Banner, Teaser
4) "Warum Sie uns wählen sollten": 5 bullet points ohne weiteren Text
5) "Aus unserem Blog": Frame für 3 Blogartikel + Bild + Datum + Header + 2-3 Zeilen Text
6) Alle drei QMSR Logos
7) Footer: Click Us (quick links), Contact Us (Adresse), Follow Us (Pinnwald, ZOLP, Kontaktor)
8) Copyright + Impressum
>>> Das Design soll klar sein, aber nicht zu kantig. Vielmehr sollen abgerundete Ecken und dynamische Elemente genutzt werden.
Architektur:
3 Ebenen:
1) Homepage
2) TAVI, Training, Coaching, Consulting, für Trainer, Kundenstimmen/Referenzen, Kontakt
3) noch zu bestimmende Produktdetailseiten
Texte werden noch erstellt, Layout kann ggf. mit Platzhaltertext gefüllt werden.
Bildmaterial: Logo und vorhandenes Imagebild werden zur Verfügung gestellt. Bilder können ggf. gekauft werden. Vorschläge erwünscht.
Corporate colors:
grün: #a2c61b + monochromatic colors
http://www.tintoskop.de/a2c61b
grau: #474747 + monochromatic colors
http://www.tintoskop.de/474747

```html
<!DOCTYPE html>
<html lang="de">
<head>
<meta charset="utf-8">
<title>TAVI Training, Coaching &amp; Consulting</title>
<link href="https://fonts.googleapis.com/css2?family=Open+Sans:wght@400;600;700&display=swap" rel="stylesheet">
<style>
:root{
  --green:#a2c61b;
  --green-light:#c4dd5c;
  --grey:#474747;
  --dark:#2a2a2a;
  --text:#222;
  --muted:#8a8a8a;
  --white:#fff;
  --badge:#0a6bbd;
}
*{margin:0;padding:0;box-sizing:border-box}
html,body{width:696px;height:1200px;overflow:hidden;background:var(--white)}
body{position:relative;font-family:"Open Sans",Arial,sans-serif;color:var(--text)}
.abs{position:absolute}
.brand{font-weight:700;font-size:22px;color:var(--grey);letter-spacing:1px;line-height:1}
.brand-sub{font-size:4.5px;color:var(--grey);margin-top:3px;letter-spacing:.2px}
.brand-dot{display:inline-block;width:9px;height:9px;border-radius:50%;background:var(--green);margin-left:3px;vertical-align:middle}
.nav{top:23px;font-weight:600;font-size:9.5px;color:var(--text);letter-spacing:.2px}
.nav.active{color:var(--green)}
.band{left:0;width:696px;background:var(--green)}
.hero{left:0;top:62px;width:696px;height:229px;background:radial-gradient(ellipse at 55% 40%,#6dae2b 0%,#2f6a14 45%,#0f2a06 100%);overflow:hidden}
.hero-arc{left:60px;top:10px;width:580px;height:460px;border-radius:50%;background:rgba(255,255,255,.08)}
.arrow{width:27px;height:27px;border-radius:50%;background:var(--green)}
.hero-title{left:125px;top:111px;font-size:19px;line-height:21.5px;color:var(--white)}
.btn{left:127px;top:186px;width:73px;height:23px;border-radius:12px;background:var(--green);font-size:5.6px;font-weight:700;color:var(--dark);display:flex;align-items:center;justify-content:center}
.bar{left:0;width:696px;background:var(--dark)}
.bar-label{font-weight:700;color:var(--green);text-align:center;width:200px;margin-left:-100px}
.photo{border-radius:50%}
.teaser-text{width:160px;font-size:8px;line-height:10.3px;color:var(--text)}
.h2{font-size:16px;color:var(--text)}
.num{width:26px;height:26px;border-radius:50%;background:var(--green);font-weight:700;font-size:10px;display:flex;align-items:center;justify-content:center}
.item-title{font-weight:700;font-size:10px;color:var(--green)}
.item-text{width:160px;font-size:7px;line-height:10.2px;color:var(--muted)}
.date{font-size:6.5px;color:var(--text)}
.badge{background:var(--badge)}
.footer{left:0;top:1107px;width:696px;height:93px;background:var(--dark)}
.f-title{font-weight:700;font-size:10.5px;color:var(--green)}
.f-link{font-size:8px;line-height:10.3px;color:var(--white)}
.f-social{font-size:8px;line-height:10.3px;color:var(--white);display:flex;align-items:center;gap:5px}
.f-social i{width:6px;height:6px;border-radius:50%;background:var(--white);display:inline-block}
</style>
</head>
<body>
<header>
  <div class="abs" style="left:45px;top:14px">
    <div class="brand">TAVI<span class="brand-dot"></span></div>
    <div class="brand-sub">Training · Coaching · Consulting</div>
  </div>
  <div class="abs badge" style="left:157px;top:19px;width:81px;height:20px"></div>
  <nav>
    <span class="abs nav active" style="left:279px">LEISTUNGEN <span style="display:inline-block;width:6px;height:6px;border-radius:50%;background:var(--green)"></span></span>
    <span class="abs nav" style="left:366px">ÜBER UNS</span>
    <span class="abs nav" style="left:434px">FÜR TRAINER ⌄</span>
    <span class="abs nav" style="left:524px">REFERENZEN</span>
    <span class="abs nav" style="left:606px">KONTAKT</span>
  </nav>
</header>

<div class="abs band" style="top:57px;height:5px"></div>
<section class="abs hero" role="img" aria-label="Nahaufnahme eines sich entrollenden grünen Farnwedels">
  <div class="abs hero-arc"></div>
</section>
<svg class="abs" style="left:46px;top:171px" width="27" height="27" viewBox="0 0 27 27"><circle cx="13.5" cy="13.5" r="13.5" fill="#a2c61b"/><path d="M15.5 7.5 L9.5 13.5 L15.5 19.5" stroke="#2a2a2a" stroke-width="3" fill="none" stroke-linecap="round"/></svg>
<svg class="abs" style="left:623px;top:171px" width="27" height="27" viewBox="0 0 27 27"><circle cx="13.5" cy="13.5" r="13.5" fill="#a2c61b"/><path d="M11.5 7.5 L17.5 13.5 L11.5 19.5" stroke="#2a2a2a" stroke-width="3" fill="none" stroke-linecap="round"/></svg>
<h1 class="abs hero-title" style="font-weight:400">Training, Coaching<br>&amp; Consulting:<br>Leicht gemacht</h1>
<div class="abs btn" style="top:248px">MEHR ERFAHREN</div>
<div class="abs band" style="top:291px;height:5px"></div>

<div class="abs bar" style="top:296px;height:27px"></div>
<span class="abs bar-label" style="left:124px;top:303px;font-size:10px">TRAINING</span>
<span class="abs bar-label" style="left:348px;top:303px;font-size:10px">COACHING</span>
<span class="abs bar-label" style="left:573px;top:303px;font-size:10px">CONSULTING</span>

<div class="abs photo" style="left:45px;top:339px;width:158px;height:158px;background:linear-gradient(180deg,#4f86ad 0%,#d9c9a6 45%,#5d6b3a 65%,#3a3f45 100%)" role="img" aria-label="Läufer auf einer Bergstraße bei Sonnenuntergang"></div>
<div class="abs photo" style="left:269px;top:339px;width:158px;height:158px;background:radial-gradient(circle at 50% 45%,#8bc34a 0%,#3f7f1e 55%,#1d4a0c 100%)" role="img" aria-label="Sich entrollender Farnwedel"></div>
<div class="abs photo" style="left:494px;top:339px;width:158px;height:158px;background:linear-gradient(180deg,#d6d6da 0%,#a9a7aa 55%,#3b3736 80%,#2a2625 100%)" role="img" aria-label="Person sitzt auf einem Felsvorsprung im Gegenlicht"></div>

<div class="abs bar" style="top:513px;height:28px"></div>
<span class="abs bar-label" style="left:121px;top:522px;font-size:7.5px">LOREM IPSUM DOLOR</span>
<span class="abs bar-label" style="left:347px;top:522px;font-size:7.5px">LOREM IPSUM DOLOR</span>
<span class="abs bar-label" style="left:573px;top:522px;font-size:7.5px">LOREM IPSUM DOLOR</span>

<p class="abs teaser-text" style="left:45px;top:555px">Durch mich gebiert das Netz die Kunst aus sich selbst heraus. Nicht schlicht reproduktiver Natur, repräsentiere ich vielmehr die kontinuierliche Evolution des Wortes.</p>
<p class="abs teaser-text" style="left:269px;top:555px">Durch mich gebiert das Netz die Kunst aus sich selbst heraus. Nicht schlicht reproduktiver Natur, repräsentiere ich vielmehr die kontinuierliche Evolution des Wortes.</p>
<p class="abs teaser-text" style="left:495px;top:555px">Durch mich gebiert das Netz die Kunst aus sich selbst heraus. Nicht schlicht reproduktiver Natur, repräsentiere ich vielmehr die kontinuierliche Evolution des Wortes.</p>

<h2 class="abs h2" style="left:83px;top:644px;font-weight:400">Warum Sie uns wählen sollten</h2>
<h2 class="abs h2" style="left:445px;top:644px;font-weight:400">Aus unserem Blog</h2>

<div class="abs num" style="left:83px;top:700px">1</div>
<h3 class="abs item-title" style="left:129px;top:696px">Grund Nummer Eins</h3>
<p class="abs item-text" style="left:129px;top:711px">Durch mich gebiert das Netz die Kunst aus sich selbst heraus. Nicht schlicht reproduktiver Natur, repräsentiere ich vielmehr die kontinuierliche Evolution des Wortes.</p>
<div class="abs num" style="left:83px;top:812px">2</div>
<h3 class="abs item-title" style="left:129px;top:809px">Grund Nummer Zwei</h3>
<p class="abs item-text" style="left:129px;top:824px">Durch mich gebiert das Netz die Kunst aus sich selbst heraus. Nicht schlicht reproduktiver Natur, repräsentiere ich vielmehr die kontinuierliche Evolution des Wortes.</p>
<div class="abs num" style="left:83px;top:923px">3</div>
<h3 class="abs item-title" style="left:129px;top:919px">Grund Nummer Drei</h3>
<p class="abs item-text" style="left:129px;top:934px">Durch mich gebiert das Netz die Kunst aus sich selbst heraus. Nicht schlicht reproduktiver Natur, repräsentiere ich vielmehr die kontinuierliche Evolution des Wortes.</p>

<div class="abs photo" style="left:350px;top:689px;width:72px;height:72px;background:linear-gradient(180deg,#4f86ad 0%,#d9c9a6 45%,#5d6b3a 65%,#3a3f45 100%)" role="img" aria-label="Läufer auf einer Bergstraße"></div>
<span class="abs date" style="left:444px;top:687px">02.02.2016</span>
<h3 class="abs item-title" style="left:444px;top:697px">Heading 01</h3>
<p class="abs item-text" style="left:444px;top:712px">Durch mich gebiert das Netz die Kunst aus sich selbst heraus. Nicht schlicht reproduktiver Natur, repräsentiere ich vielmehr die kontinuierliche Evolution des Wortes.</p>

<div class="abs photo" style="left:350px;top:801px;width:72px;height:72px;background:radial-gradient(circle at 50% 45%,#8bc34a 0%,#3f7f1e 55%,#1d4a0c 100%)" role="img" aria-label="Farnwedel"></div>
<span class="abs date" style="left:444px;top:800px">10.02.2016</span>
<h3 class="abs item-title" style="left:444px;top:810px">Heading 01</h3>
<p class="abs item-text" style="left:444px;top:825px">Durch mich gebiert das Netz die Kunst aus sich selbst heraus. Nicht schlicht reproduktiver Natur, repräsentiere ich vielmehr die kontinuierliche Evolution des Wortes.</p>

<div class="abs photo" style="left:350px;top:911px;width:72px;height:72px;background:linear-gradient(180deg,#d6d6da 0%,#a9a7aa 55%,#3b3736 80%,#2a2625 100%)" role="img" aria-label="Person auf einem Felsvorsprung"></div>
<span class="abs date" style="left:444px;top:910px">14.02.2016</span>
<h3 class="abs item-title" style="left:444px;top:920px">Heading 01</h3>
<p class="abs item-text" style="left:444px;top:935px">Durch mich gebiert das Netz die Kunst aus sich selbst heraus. Nicht schlicht reproduktiver Natur, repräsentiere ich vielmehr die kontinuierliche Evolution des Wortes.</p>

<div class="abs badge" style="left:186px;top:1030px;width:34px;height:45px"></div>
<div class="abs badge" style="left:299px;top:1031px;width:35px;height:45px"></div>
<div class="abs badge" style="left:436px;top:1040px;width:104px;height:27px"></div>

<div class="abs band" style="top:1101px;height:6px"></div>
<footer class="abs footer"></footer>
<div class="abs" style="left:45px;top:1127px">
  <div class="brand" style="color:var(--white)">TAVI<span class="brand-dot"></span></div>
  <div class="brand-sub" style="color:var(--white)">Training · Coaching · Consulting</div>
</div>
<div class="abs" style="left:190px;top:1123px">
  <div class="f-title">Click Us</div>
  <div style="margin-top:4px"><div class="f-link">Link Title Number 1</div><div class="f-link">Link Title Number 2</div><div class="f-link">Link Title Number 3</div></div>
</div>
<div class="abs" style="left:323px;top:1123px">
  <div class="f-title">Contact Us</div>
  <div style="margin-top:4px"><div class="f-link">Link Title Number 1</div><div class="f-link">Link Title Number 2</div><div class="f-link">Link Title Number 3</div></div>
</div>
<div class="abs" style="left:456px;top:1123px">
  <div class="f-title">Follow Us</div>
  <div style="margin-top:2px;margin-left:8px">
    <div class="f-social"><i></i>Pinnwald</div>
    <div class="f-social"><i></i>Zwitscher</div>
    <div class="f-social"><i></i>Zolp</div>
    <div class="f-social"><i></i>Bildhaus</div>
  </div>
</div>
<div class="abs" style="left:595px;top:1126px;font-size:7.5px;color:var(--green)">© 2016 TAVI</div>
<div class="abs" style="left:595px;top:1138px;font-size:11px;font-weight:700;color:var(--white)">Impressum</div>
</body>
</html>
```